Copper Lantern

Need a business card for our restaurant. Restaurant and Bar in the mountains of North Idaho. Rustic looking card

rustic design, wood and metal looking, primarily neutral colors

• Name, address, phone number, website, email address

```html
<!DOCTYPE html>
<html lang="en">
<head>
<meta charset="utf-8">
<title>Copper Lantern – Business Card</title>
<link href="https://fonts.googleapis.com/css2?family=Montserrat:wght@400;700&display=swap" rel="stylesheet">
<style>
  :root {
    --page-bg: #2b2b2b;
    --card-bg: #1b1b1b;
    --card-edge: #262626;
    --ink: #f2f2f2;
    --ink-soft: #d6d6d6;
  }
  * { box-sizing: border-box; margin: 0; padding: 0; }
  html, body {
    width: 1200px; height: 875px; overflow: hidden;
    background: var(--page-bg);
    font-family: "Montserrat", sans-serif;
    color: var(--ink);
  }
  .canvas {
    position: relative; width: 1200px; height: 875px;
    display: flex; align-items: center; justify-content: center; gap: 50px;
  }
  .card {
    position: relative;
    width: 525px; height: 300px;
    background: var(--card-bg);
    border: 1px solid var(--card-edge);
    border-radius: 18px;
  }
  .brand-mark {
    display: flex; align-items: center; gap: 12px;
    color: var(--ink); font-weight: 400;
  }
  .brand-mark .dot {
    border: 2px solid var(--ink); border-radius: 50%;
  }
  .card-front { display: flex; align-items: center; justify-content: center; }
  .card-front .brand-mark { font-size: 30px; letter-spacing: 3px; text-transform: uppercase; }
  .card-front .dot { width: 26px; height: 26px; }

  .card-back .brand-mark {
    position: absolute; top: 38px; right: 34px;
    font-size: 15px; letter-spacing: 2px; text-transform: uppercase;
  }
  .card-back .dot { width: 14px; height: 14px; }
  .divider {
    position: absolute; left: 34px; right: 34px; top: 108px;
    height: 1px; background: var(--ink-soft);
  }
  .address {
    position: absolute; right: 34px; top: 124px;
    text-align: right; font-size: 12px; line-height: 1.35; color: var(--ink-soft);
  }
  .person { position: absolute; left: 34px; top: 150px; }
  .person-name { font-size: 21px; font-weight: 700; line-height: 1.1; }
  .person-role { font-size: 12px; color: var(--ink-soft); margin-top: 3px; }
  .contact-list { list-style: none; margin-top: 16px; }
  .contact-list li {
    display: flex; align-items: center; gap: 9px;
    font-size: 12.5px; line-height: 1; margin-bottom: 8px; color: var(--ink-soft);
  }
  .contact-list svg { width: 12px; height: 12px; fill: var(--ink); flex: none; }
</style>
</head>
<body>
<main class="canvas">
  <section class="card card-front" aria-label="Card front">
    <div class="brand-mark"><span class="dot"></span><span>Copper Lantern</span></div>
  </section>

  <section class="card card-back" aria-label="Card back">
    <div class="brand-mark"><span class="dot"></span><span>Copper Lantern</span></div>
    <div class="divider"></div>
    <p class="address">48 Silver Ridge Road,<br>Pinecrest, USA</p>
    <div class="person">
      <h1 class="person-name">Owen Harlow</h1>
      <p class="person-role">Managing Director</p>
      <ul class="contact-list">
        <li>
          <svg viewBox="0 0 24 24" aria-hidden="true"><path d="M6.6 10.8a15 15 0 0 0 6.6 6.6l2.2-2.2c.3-.3.7-.4 1-.2 1.1.4 2.3.6 3.6.6.6 0 1 .4 1 1V20c0 .6-.4 1-1 1A17 17 0 0 1 3 4c0-.6.4-1 1-1h3.5c.6 0 1 .4 1 1 0 1.3.2 2.5.6 3.6.1.3 0 .7-.2 1z"/></svg>
          <span>(208) 555 0147</span>
        </li>
        <li>
          <svg viewBox="0 0 24 24" aria-hidden="true"><path d="M2 5h20v14H2z M4 7v.5l8 5 8-5V7l-8 5z" fill-rule="evenodd"/></svg>
          <span>hello@copperlantern.com</span>
        </li>
        <li>
          <svg viewBox="0 0 24 24" aria-hidden="true"><circle cx="12" cy="12" r="10"/></svg>
          <span>www.copperlantern.com</span>
        </li>
      </ul>
    </div>
  </section>
</main>
</body>
</html>
```